Walk Beside The River

Business Card design

Target Market(s)

People who require support in the commnity

Industry/Entity Type

Mental Health Support

Contact Information for Business Card

Mental Health Support Rosalind Tavener walkbesidetheriver@mailcove.com.au 0481 637 092 PO Box 926 Bellawarrane VIC 3917

Colors
6B429C
8869AF
B7A5CE
E3DAEB
F3F0F8

Requirements
Must have
• Logo & details listed above
Should not have
• No red or orange

```html
<!DOCTYPE html>
<html lang="en">
<head>
<meta charset="utf-8">
<title>Walk Beside The River – Business Card</title>
<link rel="stylesheet" href="https://fonts.googleapis.com/css2?family=Lato:wght@400;700;900&display=swap">
<style>
  :root {
    --purple-deep: #3f2270;
    --purple: #6B429C;
    --purple-mid: #8869AF;
    --lavender: #B7A5CE;
    --lavender-pale: #E3DAEB;
    --mist: #F3F0F8;
    --backdrop: #dcd7df;
  }
  * { margin: 0; padding: 0; box-sizing: border-box; }
  html, body {
    width: 1200px; height: 734px; overflow: hidden;
    background: var(--backdrop);
    font-family: "Lato", sans-serif;
  }
  .card {
    position: absolute; left: 40px; top: 46px;
    width: 1120px; height: 641px;
    border-radius: 30px; overflow: hidden;
    background: linear-gradient(100deg, #e9e6ec 0%, var(--mist) 35%, #ebe7ef 100%);
    box-shadow: 0 10px 30px rgba(60, 40, 90, 0.18);
  }
  .card-art { position: absolute; inset: 0; }
  .brand {
    position: absolute; left: 78px; top: 150px;
    display: flex; align-items: center; gap: 18px;
  }
  .brand-dot {
    width: 58px; height: 58px; border-radius: 50%;
    background: var(--purple);
    flex: none;
  }
  .brand-name {
    font-weight: 900; font-size: 34px; line-height: 1.1;
    color: var(--purple); text-transform: uppercase; letter-spacing: 1px;
  }
  .details {
    position: absolute; right: 59px; top: 336px;
    text-align: right; color: var(--lavender-pale);
  }
  .person-name {
    font-weight: 900; font-size: 49px; line-height: 1; letter-spacing: 0.5px;
    text-transform: uppercase;
  }
  .person-role { font-size: 28px; line-height: 1; margin-top: 8px; letter-spacing: 0.5px; }
  .contact { list-style: none; margin-top: 34px; }
  .contact li {
    display: flex; justify-content: flex-end; align-items: center; gap: 16px;
    line-height: 1;
  }
  .contact .phone { font-size: 33px; font-weight: 700; letter-spacing: 0.5px; }
  .contact .email { font-size: 25px; margin-top: 16px; letter-spacing: 0.3px; }
  .contact .address { font-size: 25px; margin-top: 16px; letter-spacing: 0.3px; }
  .icon { width: 26px; height: 26px; flex: none; }
</style>
</head>
<body>
  <main class="card">
    <svg class="card-art" viewBox="0 0 1120 641" width="1120" height="641" aria-hidden="true">
      <defs>
        <linearGradient id="panelFill" x1="0" y1="0" x2="1" y2="0">
          <stop offset="0" stop-color="#8869AF"/>
          <stop offset="0.18" stop-color="#5a3690"/>
          <stop offset="0.45" stop-color="#3f2270"/>
          <stop offset="1" stop-color="#5e3d8e"/>
        </linearGradient>
      </defs>
      <circle class="panel" cx="840" cy="558" r="411" fill="url(#panelFill)"/>
      <path class="swoosh" d="M407,567 Q440,235 845,178 Q515,215 415,520 Z" fill="#4a2a7e"/>
    </svg>

    <div class="brand">
      <span class="brand-dot"></span>
      <span class="brand-name">Walk Beside<br>The River</span>
    </div>

    <section class="details">
      <h1 class="person-name">Rosalind Tavener</h1>
      <p class="person-role">Mental Health Support</p>
      <ul class="contact">
        <li class="phone">0481 637 092
          <svg class="icon" viewBox="0 0 24 24" fill="none" stroke="currentColor" stroke-width="2" stroke-linecap="round" stroke-linejoin="round"><path d="M5 3h3l2 5-2.5 1.5a11 11 0 0 0 7 7L16 14l5 2v3a2 2 0 0 1-2 2A16 16 0 0 1 3 5a2 2 0 0 1 2-2z"/><path d="M15 3a6 6 0 0 1 6 6"/><path d="M15 7a2 2 0 0 1 2 2"/></svg>
        </li>
        <li class="email">walkbesidetheriver@mailcove.com.au
          <svg class="icon" viewBox="0 0 24 24" fill="none" stroke="currentColor" stroke-width="2" stroke-linejoin="round"><rect x="2" y="5" width="20" height="14" rx="1"/><path d="M2 6l10 7 10-7"/></svg>
        </li>
        <li class="address">PO Box 926 Bellawarrane VIC 3917
          <svg class="icon" viewBox="0 0 24 24" fill="none" stroke="currentColor" stroke-width="2"><path d="M12 22s7-7.5 7-13a7 7 0 0 0-14 0c0 5.5 7 13 7 13z"/><circle cx="12" cy="9" r="2.5"/></svg>
        </li>
      </ul>
    </section>
  </main>
</body>
</html>
```